Cozy Cradle Loops Needs a Beautiful Website

I need a new website for this new E-commerce. I sell handmade baby crochets, e.g. booties, headbands, hats, etc. I need a feminine and soft design to make the moms-to-be say 'oohh ahh'. I'd like pink, blue and gray. I'd like an inviting homepage, and nice regular pages where people can see and order the products.

Industry/Entity Type

Baby

Requirements
Must have
• beautiful, soft, feminine design. Please use pictures of the colors I'd like: brown, yellow, pink and blue. Any combination, but definitely include brown.

```html
<!DOCTYPE html>
<html lang="en">
<head>
<meta charset="utf-8">
<title>Cozy Cradle Loops – Handmade Baby Crochets</title>
<link href="https://fonts.googleapis.com/css2?family=Lobster&family=Open+Sans:wght@400;600&family=Oswald:wght@400&display=swap" rel="stylesheet">
<style>
:root{
  --pink:#ee3188;
  --pink-dark:#d21f72;
  --blue:#2ec3e6;
  --orange:#f7941d;
  --grass:#9fcb3a;
  --sky:#f7f7f5;
  --text:#666;
  --muted:#999;
  --dark:#333;
  --darker:#262626;
  --white:#fff;
}
*{box-sizing:border-box;margin:0;padding:0}
html,body{width:673px;height:1200px;overflow:hidden;background:var(--white)}
body{position:relative;font-family:'Open Sans',sans-serif;color:var(--text)}
.abs{position:absolute}
.script{font-family:'Lobster',cursive}

/* header */
.header-scene{left:0;top:0;width:673px;height:160px;
  background:linear-gradient(180deg,var(--sky) 0%,#f3f3ee 55%,#c8e27a 75%,var(--grass) 100%)}
.logo{left:31px;top:22px;font-family:'Lobster',cursive;font-size:30px;color:var(--pink);line-height:1}
.account-links{right:32px;top:18px;display:flex;gap:24px;font-size:9px;color:#777}

.main-nav{left:31px;top:159px;width:536px;height:33px;background:var(--pink);
  border:1px dashed rgba(255,255,255,.5);outline:2px solid var(--pink);
  display:flex;align-items:center;justify-content:space-around;padding:0 6px}
.main-nav a{font-family:'Lobster',cursive;color:var(--white);font-size:13px;text-decoration:none}
.nav-btn{top:159px;width:34px;height:33px;display:flex;align-items:center;justify-content:center}
.nav-search{left:569px;background:var(--blue)}
.nav-cart{left:607px;background:var(--orange)}

/* hero */
.hero{left:31px;top:212px;width:610px;height:282px;
  background:linear-gradient(90deg,#cfd9dc 0%,#e6e6e6 45%,#efefef 100%)}
.hero-photo{left:31px;top:212px;width:310px;height:282px;
  background:radial-gradient(ellipse at 45% 45%,#a9cfd8 0%,#bcd8df 45%,#dfe5e6 75%,transparent 100%)}
.hero-badge{left:347px;top:233px;width:250px;height:250px;border-radius:50%;
  background:rgba(255,255,255,.88);text-align:center;padding-top:46px}
.hero-badge .brand{font-family:'Lobster',cursive;color:var(--pink);font-size:24px}
.hero-badge h1{font-family:'Lobster',cursive;font-weight:400;color:#333;font-size:27px;margin-top:6px}
.hero-badge p{font-size:7.5px;line-height:13px;color:#777;width:180px;margin:8px auto 0}
.hero-cta{width:30px;height:30px;border-radius:50%;background:var(--pink);margin:12px auto 0;
  display:flex;align-items:center;justify-content:center}
.hero-arrow{top:349px;width:24px;height:24px;border-radius:50%;background:rgba(60,60,60,.75);
  display:flex;align-items:center;justify-content:center}

/* categories */
.category{top:513px;width:195px;height:114px;border:3px solid #f1f1f1;display:flex;
  flex-direction:column;align-items:center;justify-content:center}
.category .cart-ring{width:34px;height:34px;border-radius:50%;background:rgba(60,60,60,.6);
  border:2px solid rgba(255,255,255,.7);display:flex;align-items:center;justify-content:center}
.category span{font-family:'Lobster',cursive;color:var(--white);font-size:17px;margin-top:2px}

/* featured */
.section-title{left:31px;top:642px;font-family:'Lobster',cursive;color:var(--pink);font-size:18px}
.slider-dots{right:31px;top:650px;display:flex;gap:5px}
.slider-dots i{width:12px;height:12px;border-radius:50%;border:1px solid #ccc;display:block}
.product{top:680px;width:145px;height:208px;border:1px solid #eee;background:var(--white)}
.product .photo{height:104px}
.product h3{font-weight:400;font-size:13px;color:#666;margin:12px 0 0 11px;display:flex;justify-content:space-between;padding-right:11px}
.product h3 small{color:var(--orange);font-size:7px;letter-spacing:1px;line-height:18px}
.product p{font-size:8.5px;line-height:14px;color:var(--muted);margin:10px 11px 0;text-align:justify}
.price-bar{position:absolute;left:-1px;right:-1px;bottom:-1px;height:27px;background:var(--pink);
  display:flex;justify-content:space-between;align-items:center;padding:0 12px;
  font-family:'Oswald',sans-serif;color:var(--white);font-size:11px}

/* footer */
.footer-main{left:31px;top:912px;width:610px;height:164px;background:var(--blue);color:var(--white)}
.footer-logo{left:13px;top:20px;font-family:'Lobster',cursive;color:var(--pink);font-size:22px}
.contact-row{left:13px;display:flex;align-items:center;gap:11px;font-size:8.5px;line-height:14px}
.contact-row .icon{width:24px;height:24px;border:1px solid rgba(255,255,255,.7);display:flex;align-items:center;justify-content:center}
.footer-col{top:26px;font-size:7.5px;line-height:14.5px}
.footer-col h4{font-weight:400;font-size:11px;letter-spacing:.3px;margin-bottom:7px}

.footer-bar{left:31px;top:1076px;width:610px;height:60px;background:var(--dark);color:#ddd}
.news-icon{left:10px;top:16px;width:28px;height:28px;border-radius:50%;background:#2a2a2a;display:flex;align-items:center;justify-content:center}
.news-label{left:52px;top:22px;font-size:8.5px;line-height:14px;letter-spacing:.4px}
.news-input{left:125px;top:23px;width:120px;height:22px;background:#2b2b2b;border:1px solid #3a3a3a;font-size:6px;color:#777;padding:7px 9px}
.news-btn{left:252px;top:22px;width:56px;height:23px;background:#1e9ad6;color:var(--white);font-size:7px;font-weight:600;display:flex;align-items:center;justify-content:center;border-radius:2px}
.pay-label{left:340px;top:29px;font-size:8.5px;letter-spacing:.4px}
.pay-cards{left:403px;top:22px;display:flex;gap:6px}
.pay-cards i{width:33px;height:20px;background:#bdbdbd;border-radius:2px;display:block}

.footer-bottom{left:31px;top:1136px;width:610px;height:41px;background:var(--darker);color:#999;font-size:7.5px}
.footer-bottom .copy{left:14px;top:15px}
.socials{left:303px;top:10px;display:flex;gap:6px}
.socials i{width:19px;height:19px;border:1px solid #666;border-radius:50%;display:block}
.footer-bottom .legal{right:14px;top:15px}
</style>
</head>
<body>

<header>
  <div class="abs header-scene" role="img" aria-label="Illustrated meadow with green hills, trees, a rainbow and stars"></div>
  <div class="abs logo">Cozy Cradle Loops</div>
  <nav class="abs account-links"><span>My Account</span><span>Create an Account</span><span>Log in</span></nav>

  <nav class="abs main-nav">
    <a>Home</a><a>Baby Crochets</a><a>Booties &amp; Accessories</a><a>Headbands</a><a>Selling</a><a>Contact</a>
  </nav>
  <div class="abs nav-btn nav-search">
    <svg width="12" height="12" viewBox="0 0 12 12" fill="none" stroke="#fff" stroke-width="1.5"><circle cx="5" cy="5" r="3.6"/><path d="M7.6 7.6L11 11"/></svg>
  </div>
  <div class="abs nav-btn nav-cart">
    <svg width="16" height="14" viewBox="0 0 16 14" fill="none" stroke="#fff" stroke-width="1.6"><path d="M1 1h2.5l2 8h7.5l1.5-6H4.4"/><circle cx="6.5" cy="12" r="1.2"/><circle cx="12" cy="12" r="1.2"/></svg>
  </div>
</header>

<section>
  <div class="abs hero"></div>
  <div class="abs hero-photo" role="img" aria-label="Pale blue crocheted baby newsboy cap with white band and button"></div>
  <div class="abs hero-badge">
    <div class="brand">Cozy Cradle Loops</div>
    <h1>Baby crochets</h1>
    <p>Lorem ipsum dolor sit amet, consectetur adipisicing elit, sed do eiusmod tempor incididunt ut labore et dolore magna aliqua.</p>
    <div class="hero-cta"><svg width="14" height="12" viewBox="0 0 14 12" fill="none" stroke="#fff" stroke-width="1.4"><path d="M1 4h12l-1.5 7h-9z"/><path d="M4 4l3-3 3 3"/></svg></div>
  </div>
  <div class="abs hero-arrow" style="left:62px"><svg width="8" height="10" viewBox="0 0 8 10" fill="none" stroke="#fff" stroke-width="1.6"><path d="M6 1L2 5l4 4"/></svg></div>
  <div class="abs hero-arrow" style="left:596px"><svg width="8" height="10" viewBox="0 0 8 10" fill="none" stroke="#fff" stroke-width="1.6"><path d="M2 1l4 4-4 4"/></svg></div>
</section>

<section>
  <div class="abs category" style="left:31px;background:linear-gradient(135deg,#6f7280,#3f4a66 60%,#8a8d96)" role="img" aria-label="Navy crocheted baby sneakers">
    <div class="cart-ring"><svg width="14" height="12" viewBox="0 0 16 14" fill="none" stroke="#fff" stroke-width="1.6"><path d="M1 1h2.5l2 8h7.5l1.5-6H4.4"/><circle cx="6.5" cy="12" r="1.2"/><circle cx="12" cy="12" r="1.2"/></svg></div>
    <span>Sneaker Blue</span>
  </div>
  <div class="abs category" style="left:239px;background:linear-gradient(135deg,#a7a4a0,#e6e1cf 55%,#b98a86)" role="img" aria-label="Ivory crocheted baby shoes with pink roses">
    <div class="cart-ring"><svg width="14" height="12" viewBox="0 0 16 14" fill="none" stroke="#fff" stroke-width="1.6"><path d="M1 1h2.5l2 8h7.5l1.5-6H4.4"/><circle cx="6.5" cy="12" r="1.2"/><circle cx="12" cy="12" r="1.2"/></svg></div>
    <span>Ivory Shows</span>
  </div>
  <div class="abs category" style="left:447px;background:linear-gradient(135deg,#d6cfd0,#eac9d0 50%,#d89aa8)" role="img" aria-label="Pink crocheted ballet slippers with roses">
    <div class="cart-ring"><svg width="14" height="12" viewBox="0 0 16 14" fill="none" stroke="#fff" stroke-width="1.6"><path d="M1 1h2.5l2 8h7.5l1.5-6H4.4"/><circle cx="6.5" cy="12" r="1.2"/><circle cx="12" cy="12" r="1.2"/></svg></div>
    <span>Pink Ballet</span>
  </div>
</section>

<section>
  <h2 class="abs section-title" style="font-weight:400">Featured Products</h2>
  <div class="abs slider-dots"><i></i><i></i></div>

  <article class="abs product" style="left:31px">
    <div class="photo" style="background:linear-gradient(180deg,#fafafa,#f4c6e3 50%,#f7f7f7)" role="img" aria-label="Pink crocheted baby crown headband"></div>
    <h3>Baby Crochets <small>★★★☆</small></h3>
    <p>Pellentesque habitant morbi tristique senectus et netus</p>
    <div class="price-bar"><span>$7.99</span><svg width="11" height="10" viewBox="0 0 14 12" fill="none" stroke="#fff" stroke-width="1.4"><path d="M1 4h12l-1.5 7h-9z"/><path d="M4 4l3-3 3 3"/></svg></div>
  </article>
  <article class="abs product" style="left:186px">
    <div class="photo" style="background:linear-gradient(160deg,#e0dcdc,#eec6cf 55%,#d9d4d4)" role="img" aria-label="Pink crocheted ballet shoes with roses"></div>
    <h3>Pink ballet <small>★★★☆</small></h3>
    <p>Pellentesque habitant morbi tristique senectus et netus</p>
    <div class="price-bar"><span>$7.99</span><svg width="11" height="10" viewBox="0 0 14 12" fill="none" stroke="#fff" stroke-width="1.4"><path d="M1 4h12l-1.5 7h-9z"/><path d="M4 4l3-3 3 3"/></svg></div>
  </article>
  <article class="abs product" style="left:341px">
    <div class="photo" style="background:linear-gradient(160deg,#bdbdbd,#2b2a2a 50%,#8e8e8e)" role="img" aria-label="Black crocheted baby sneakers with white laces"></div>
    <h3>Sneaker black <small>★★★☆</small></h3>
    <p>Pellentesque habitant morbi tristique senectus et netus</p>
    <div class="price-bar"><span>$7.99</span><svg width="11" height="10" viewBox="0 0 14 12" fill="none" stroke="#fff" stroke-width="1.4"><path d="M1 4h12l-1.5 7h-9z"/><path d="M4 4l3-3 3 3"/></svg></div>
  </article>
  <article class="abs product" style="left:497px">
    <div class="photo" style="background:linear-gradient(160deg,#c9a6a6,#6e5a52 50%,#bbb)" role="img" aria-label="Brown and gray crocheted baby sneakers"></div>
    <h3>Sneaker gray <small>★★★☆</small></h3>
    <p>Pellentesque habitant morbi tristique senectus et netus</p>
    <div class="price-bar"><span>$7.99</span><svg width="11" height="10" viewBox="0 0 14 12" fill="none" stroke="#fff" stroke-width="1.4"><path d="M1 4h12l-1.5 7h-9z"/><path d="M4 4l3-3 3 3"/></svg></div>
  </article>
</section>

<footer>
  <div class="abs footer-main">
    <div class="abs footer-logo">Cozy Cradle Loops</div>
    <div class="abs contact-row" style="top:68px">
      <div class="icon"><svg width="10" height="13" viewBox="0 0 10 13" fill="none" stroke="#fff" stroke-width="1.3"><path d="M5 12S1 7.5 1 5a4 4 0 018 0c0 2.5-4 7-4 7z"/><circle cx="5" cy="5" r="1.4"/></svg></div>
      <span>14 Willow Lane Hartfield<br>Cozy Cradle Loops HF2 9QB</span>
    </div>
    <div class="abs contact-row" style="top:99px">
      <div class="icon"><svg width="12" height="12" viewBox="0 0 12 12" fill="#fff"><path d="M2 1h2.5l1 2.8-1.5 1a6 6 0 003.2 3.2l1-1.5 2.8 1V10a1 1 0 01-1 1A9.5 9.5 0 011 2a1 1 0 011-1z"/></svg></div>
      <span>Phone : 10 482 77 215 306</span>
    </div>
    <div class="abs contact-row" style="top:130px">
      <div class="icon"><svg width="13" height="9" viewBox="0 0 13 9" fill="none" stroke="#fff" stroke-width="1.2"><rect x=".6" y=".6" width="11.8" height="7.8"/><path d="M.6.6l5.9 4.5L12.4.6"/></svg></div>
      <span style="font-size:10px">hello@cozycradleloops.com</span>
    </div>
    <div class="abs footer-col" style="left:219px"><h4>INFORMATION</h4>Baby Shoes<br>Baby crochets<br>booties<br>headbands</div>
    <div class="abs footer-col" style="left:357px"><h4>CUSTOMER SUPPORT</h4>Contact Us<br>Shipping &amp; Returns<br>Privacy Notice<br>Conditions of Use</div>
    <div class="abs footer-col" style="left:525px"><h4>MY ACCOUNT</h4>My Rewards<br>Register<br>About Rewards<br>Rewards FAQ</div>
  </div>

  <div class="abs footer-bar">
    <div class="abs news-icon"><svg width="14" height="10" viewBox="0 0 13 9" fill="none" stroke="#999" stroke-width="1.2"><rect x=".6" y=".6" width="11.8" height="7.8"/><path d="M.6.6l5.9 4.5L12.4.6"/></svg></div>
    <div class="abs news-label">NEWSLETTER<br>SIGN UP</div>
    <div class="abs news-input">Enter Your Email</div>
    <div class="abs news-btn">SUBSCRIBE</div>
    <div class="abs pay-label">PAYMENTS</div>
    <div class="abs pay-cards" aria-label="Accepted payment methods"><i></i><i></i><i></i><i></i><i></i></div>
  </div>

  <div class="abs footer-bottom">
    <div class="abs copy">©2013 - 2014 Cozy Cradle Loops.. All Rights Reserved.</div>
    <div class="abs socials" aria-label="Social links"><i></i><i></i><i></i></div>
    <div class="abs legal">Terms of Service | Privacy Policy</div>
  </div>
</footer>

</body>
</html>
```